Bramblewick Homes Tarrow Customer Brochure

Need a brochure designed that is clean and minimal that contains our logo, and contact information. Would like an area where we could insert business cards, and slips on both sides of the openings to place sheets of paper in. Would prefer to have the COVER LETTER I have attached printed on one side of the opening.

Target Market(s)

Home buyers

Font styles to use
Sans Serif

Colors

Designer to choose colors to be used in the design.

Requirements
Must have
• Logo, contact info, website, etc. Must be minimal in design and very clean looking.
Nice to have
• Please see above
Should not have
• No stock pictures of homes, builds, etc. Need it to look very clean

```html
<!DOCTYPE html>
<html lang="en">
<head>
<meta charset="utf-8">
<title>Bramblewick Homes Tarrow – Pocket Folder Inside Spread</title>
<link rel="stylesheet" href="https://fonts.googleapis.com/css2?family=Archivo:wght@700&display=swap">
<style>
  :root {
    --backdrop: #7a7a7a;
    --pocket: #f7f7f7;
    --photo-light: #f1f1f1;
    --photo-mid: #dcdcdc;
    --photo-dark: #c4c4c4;
    --dieline: #5ec3e6;
    --slit: #e0463c;
    --ink: #1c1c1c;
    --accent: #c9a06e;
    --gutter-shade: rgba(0,0,0,0.08);
  }
  html, body {
    margin: 0;
    width: 1200px;
    height: 833px;
    overflow: hidden;
    background: var(--backdrop);
  }
  .folder-spread {
    position: absolute;
    left: 60px;
    top: 66px;
    width: 1080px;
    height: 700px;
    box-shadow: 0 12px 30px rgba(0,0,0,0.35);
  }
  .folder-spread svg { display: block; }
  .brand-name, .contact-line {
    font-family: "Archivo", sans-serif;
    font-weight: 700;
    fill: var(--ink);
  }
  .brand-name { font-size: 22px; letter-spacing: 1px; }
  .brand-name--sub { letter-spacing: 8px; }
  .contact-line { font-size: 10px; letter-spacing: 0.5px; }
</style>
</head>
<body>
  <div class="folder-spread">
    <svg width="1080" height="700" viewBox="0 0 1080 700" xmlns="http://www.w3.org/2000/svg">
      <defs>
        <linearGradient id="interior-tones-left" x1="0" y1="0" x2="1" y2="1">
          <stop offset="0" stop-color="var(--photo-light)"/>
          <stop offset="0.6" stop-color="var(--photo-mid)"/>
          <stop offset="1" stop-color="var(--photo-dark)"/>
        </linearGradient>
        <linearGradient id="interior-tones-right" x1="1" y1="0" x2="0" y2="1">
          <stop offset="0" stop-color="var(--photo-light)"/>
          <stop offset="0.55" stop-color="var(--photo-mid)"/>
          <stop offset="1" stop-color="var(--photo-dark)"/>
        </linearGradient>
        <linearGradient id="gutter" x1="0" y1="0" x2="1" y2="0">
          <stop offset="0" stop-color="rgba(0,0,0,0)"/>
          <stop offset="0.5" stop-color="var(--gutter-shade)"/>
          <stop offset="1" stop-color="rgba(0,0,0,0)"/>
        </linearGradient>
      </defs>

      <rect class="panel-image" x="0" y="0" width="540" height="700" fill="url(#interior-tones-left)"
            role="img" aria-label="Faded black and white photo of a bright kitchen with pendant lights and a stone island"/>
      <rect class="panel-image" x="540" y="0" width="540" height="700" fill="url(#interior-tones-right)"
            role="img" aria-label="Faded black and white photo of an open living and dining room with a chandelier"/>

      <!-- left pocket -->
      <path class="pocket" d="M0 520 Q300 470 540 395 L540 700 L0 700 Z" fill="var(--pocket)"/>
      <path class="dieline" d="M14 700 L14 528 Q300 478 530 404" fill="none" stroke="var(--dieline)" stroke-width="1"/>

      <g class="card-slits" stroke="var(--slit)" stroke-width="1.5">
        <line x1="330" y1="470" x2="375" y2="488"/>
        <line x1="220" y1="520" x2="205" y2="560"/>
        <line x1="400" y1="520" x2="385" y2="555"/>
        <line x1="215" y1="625" x2="260" y2="640"/>
      </g>

      <!-- right pocket -->
      <path class="pocket" d="M540 700 L540 470 Q540 430 585 430 L1080 430 L1080 700 Z" fill="var(--pocket)"/>
      <path class="dieline" d="M552 700 L552 478 Q552 442 592 442 L1068 442 L1068 700" fill="none" stroke="var(--dieline)" stroke-width="1"/>

      <!-- brand lockup -->
      <rect class="brand-square" x="779" y="476" width="60" height="60" fill="var(--accent)"/>
      <text class="brand-name" x="809" y="570" text-anchor="middle">BRAMBLEWICK</text>
      <text class="brand-name brand-name--sub" x="813" y="594" text-anchor="middle">HOMES</text>

      <!-- contact details -->
      <text class="contact-line" x="809" y="630" text-anchor="middle">905 555 0142  ·  hello@bramblewickhomes.example</text>
      <text class="contact-line" x="809" y="646" text-anchor="middle">www.bramblewickhomes.example</text>

      <rect class="gutter-fold" x="520" y="0" width="40" height="700" fill="url(#gutter)"/>
    </svg>
  </div>
</body>
</html>
```